Hi,
We are also sourcing for a logo, if you have ideas please take a look at our other project (if you look at our profile you should be able to see it).
We are looking for a website that will be used to manage mobile devices. The feature set is rather small, users can Wipe, Lock, Locate devices as well as make them Ring or Speak (by sending text to be spoken). We attached some images of what it looks like right now. We are looking for simplicity, uniformity and most importantly, the website should be thought of as primary User Interface, it should flow.
Please see attached to get an idea of what it looks like now. The current design was inspired by making a site that will work and flow well on a variety of displays (from mobile to tablet to desktop).
We want to stay away from radio buttons, check-boxes. This should be engaging and creative, opposite of Corporate. Not busy (ideally we are looking to have fewest possible choices at any given time and at the same time no feature should be more than 3 clicks away (this is a suggestion/approximation... just want to share our understanding of what 'flow' is).
Could be cartoony.
Thanks!
BrisketLoom
Reason: there are a couple of designs that are interesting, in addition to specific feedback I provided, possibly looking for more concepts.
Thank You

```html
<!DOCTYPE html>
<html lang="en">
<head>
<meta charset="utf-8">
<title>BrisketLoom – Location</title>
<link rel="stylesheet" href="https://fonts.googleapis.com/css2?family=Questrial&family=Arimo:wght@400&family=Open+Sans:wght@700&display=swap">
<style>
  :root {
    --black: #000000;
    --orange: #e88000;
    --orange-light: #f29c33;
    --orange-dark: #cf6f08;
    --white: #ffffff;
    --ink: #111111;
    --paper: #f6f4ef;
    --map-green: #d9e3c8;
    --map-road: #f2d27a;
  }
  * { box-sizing: border-box; margin: 0; padding: 0; }
  html, body { width: 1200px; height: 874px; overflow: hidden; }
  body { position: relative; background: var(--white); font-family: "Arimo", Arial, sans-serif; color: var(--ink); }

  .topbar { position: absolute; left: 0; top: 0; width: 1200px; height: 60px; background: var(--black); }
  .brand { position: absolute; left: 142px; top: 8px; font-family: "Questrial", sans-serif; font-size: 40px; color: var(--white); letter-spacing: -0.5px; }
  .main-nav { position: absolute; top: 15px; left: 652px; display: flex; gap: 0; font-family: "Questrial", sans-serif; font-size: 20px; }
  .main-nav a { color: var(--white); text-decoration: none; height: 33px; line-height: 33px; padding: 0 14px; border-radius: 12px; margin-right: 3px; }
  .main-nav a.is-active { background: var(--orange); margin-right: 3px; }
  .main-nav a:nth-child(3) { margin-right: 3px; }

  .hero { position: absolute; left: 0; top: 60px; width: 1200px; height: 568px;
    background: radial-gradient(ellipse 230px 140px at 350px 10px, rgba(255,230,190,0.7), rgba(255,230,190,0) 100%), var(--orange); }
  .tool-nav { position: absolute; left: 144px; top: 18px; display: flex; font-size: 19px; }
  .tool-nav a { color: var(--ink); text-decoration: none; height: 33px; line-height: 33px; padding: 0 16px; border-radius: 14px; margin-right: 3px; }
  .tool-nav a.is-active { background: var(--black); color: var(--white); margin-right: 5px; }
  .account-nav { position: absolute; left: 728px; top: 0; width: 318px; height: 37px; background: var(--orange-light); border-radius: 0 0 12px 12px;
    font-family: "Questrial", sans-serif; font-size: 14px; }
  .account-nav a { position: absolute; top: 10px; color: var(--white); text-decoration: none; }

  .section-title { position: absolute; left: 0; top: 68px; width: 1200px; height: 62px; background: rgba(190,100,0,0.35); }
  .section-title h1 { position: absolute; left: 155px; top: 2px; font-family: "Questrial", sans-serif; font-weight: 400; font-size: 52px; color: var(--white); }

  .intro { position: absolute; font-size: 15px; line-height: 30px; }
  .intro-a { left: 157px; top: 151px; }
  .intro-b { left: 155px; top: 245px; }

  .get-app { position: absolute; left: 152px; top: 399px; width: 299px; height: 53px; background: #141414; border: 2px solid #f0a040; border-radius: 4px; overflow: hidden; }
  .get-app span { position: absolute; left: 15px; top: 12px; font-family: "Open Sans", sans-serif; font-weight: 700; font-size: 21px; color: var(--white); }
  .get-app svg { position: absolute; right: 0; top: 0; }

  .map { position: absolute; left: 537px; top: 204px; width: 516px; height: 468px; background: var(--white); border: 1px solid #ddd; padding: 4px; }
  .map-fill { width: 100%; height: 100%; background: linear-gradient(135deg, var(--map-green), #efeadb 45%, var(--map-road) 100%); }

  .welcome { position: absolute; left: 158px; top: 684px; font-family: "Questrial", sans-serif; font-weight: 400; font-size: 44px; color: var(--black); }
  .welcome-text { position: absolute; left: 163px; top: 742px; width: 880px; font-size: 15px; line-height: 18px; }

  .band { position: absolute; left: 0; top: 792px; width: 1200px; height: 21px; background: var(--paper); }
  .band::after { content: ""; position: absolute; left: 150px; right: 80px; top: 0; height: 12px; border-radius: 50%; box-shadow: 0 8px 10px -6px rgba(0,0,0,0.35); }

  .footer { position: absolute; left: 0; top: 813px; width: 1200px; height: 61px; background: var(--black); }
  .footer-nav { position: absolute; left: 153px; top: 20px; display: flex; gap: 23px; font-family: "Questrial", sans-serif; font-size: 15px; }
  .footer-nav a { color: var(--white); text-decoration: none; }
  .copyright { position: absolute; left: 852px; top: 11px; font-size: 12px; color: var(--white); }
  .social { position: absolute; left: 942px; top: 37px; display: flex; gap: 4px; }
  .social span { width: 20px; height: 20px; background: var(--orange); border-radius: 2px; }
</style>
</head>
<body>
  <header class="topbar">
    <div class="brand">BrisketLoom</div>
    <nav class="main-nav">
      <a class="is-active" href="#">Home</a>
      <a href="#">About</a>
      <a href="#">Get Application</a>
      <a href="#">Contact</a>
    </nav>
  </header>

  <main class="hero">
    <nav class="tool-nav">
      <a class="is-active" href="#">Wipe</a>
      <a href="#">Lock</a>
      <a href="#">Find</a>
      <a href="#">Ring</a>
      <a href="#">Speak</a>
      <a href="#">Loading</a>
    </nav>
    <nav class="account-nav">
      <a href="#" style="left:27px">Admin</a>
      <a href="#" style="left:88px">Devices</a>
      <a href="#" style="left:159px">Settings</a>
      <a href="#" style="left:236px">Sign out</a>
    </nav>

    <div class="section-title"><h1>Location</h1></div>

    <p class="intro intro-a">Lorem ipsum dolor sit amet, consectetur adipiscing elit.<br>Mauris id erat non nibh semper tincidunt id eu massa.<br>Quisque sit amet nibh sit amet erat tincidunt mollis.</p>
    <p class="intro intro-b">Lorem ipsum dolor sit amet, consectetur adipiscing elit.<br>Mauris id erat non nibh semper tincidunt id eu massa.<br>Quisque sit amet nibh sit amet erat tincidunt mollis.</p>

    <a class="get-app" href="#">
      <span>Get the Application</span>
      <svg width="72" height="49" viewBox="0 0 72 49">
        <polygon points="28,0 72,0 72,49 28,49 0,24.5" fill="#ffffff"/>
        <rect x="30" y="11" width="28" height="28" rx="3" fill="#f07d10"/>
        <path d="M44 20 v10 M40 26 l4 4 l4 -4" stroke="#ffffff" stroke-width="2" fill="none"/>
      </svg>
    </a>
  </main>

  <div class="map"><div class="map-fill" role="img" aria-label="Street map showing the located device with a pin and an info bubble"></div></div>

  <h2 class="welcome">Welcome to</h2>
  <p class="welcome-text">Lorem ipsum dolor sit amet, consectetur adipiscing elit. Mauris id erat non nibh semper tincidunt id eu massa. Quisque sit amet nibh sit amet erat tincidunt mollis.</p>

  <div class="band"></div>

  <footer class="footer">
    <nav class="footer-nav">
      <a href="#">Home</a>
      <a href="#">About</a>
      <a href="#">Get Application</a>
      <a href="#">Contact</a>
    </nav>
    <div class="copyright">© 2012.www.brisketloom.com</div>
    <div class="social"><span></span><span></span><span></span></div>
  </footer>
</body>
</html>
```